Website Re-design for Kids Playhouse Business

Need current website which looks very outdated to be re-designed to look modern and contemporary, reduce clutter significantly and make it look elegant and simple.
Current website: http://www.tumblenest.com.au/
A website which the business owner likes, use as reference/inspiration: http://vexa.com.au/
Looking for light green palette, natural colours. "WHAT'S ON" page/link no longer required.
Industry/Entity Type
Business
Number of Pages Required
5+ page
Look and feel
Each slider illustrates characteristics of the customer's brand and the style your logo design should communicate.

```html
<!DOCTYPE html>
<html lang="en">
<head>
<meta charset="utf-8">
<title>Tumble Nest Playhouse &amp; Cafe</title>
<link rel="stylesheet" href="https://fonts.googleapis.com/css2?family=Fredoka:wght@500;600&family=Montserrat:wght@400;600;700&family=Playfair+Display:ital,wght@1,700&display=swap">
<style>
:root{
  --lime:#b9d42a;
  --mint:#e9fcd0;
  --leaf:#5d8c2e;
  --leaf-dark:#4d7627;
  --feature-green:#76a64c;
  --sage:#aecb98;
  --footer-green:#6b9b44;
  --box-sage:#b8c9a4;
  --text:#3b3b3b;
  --white:#ffffff;
}
*{box-sizing:border-box;margin:0;padding:0}
html,body{width:1200px;height:3679px;overflow:hidden}
body{position:relative;font-family:"Montserrat",sans-serif;color:var(--text);background:var(--mint)}
.abs{position:absolute}
.heading{font-family:"Fredoka",sans-serif;font-weight:600}

/* hero */
.hero{left:0;top:0;width:1200px;height:552px;background:linear-gradient(180deg,#7a6a63 0%,#b59a86 35%,#c98a6f 65%,#7b5a4d 100%)}
.menu-toggle{left:118px;top:46px;width:32px}
.menu-toggle span{display:block;height:5px;margin-bottom:6px;background:var(--lime);border-radius:2px}
.brand{left:186px;top:28px;color:var(--white);font-family:"Fredoka",sans-serif;font-weight:500;line-height:1}
.brand .name{font-size:38px;letter-spacing:1px}
.brand .tag{font-size:21px;margin-top:2px}
.eclub-btn{left:790px;top:42px;width:138px;height:32px;background:var(--lime);color:var(--white);font-weight:700;font-size:14px;line-height:32px;text-align:center;border-radius:3px}
.hero-phone{left:942px;top:42px;line-height:32px;color:var(--white);font-weight:700;font-size:16px}
.hero-title{left:0;top:228px;width:1200px;text-align:center;font-family:"Playfair Display",serif;font-style:italic;font-weight:700;font-size:54px;color:var(--lime)}

/* about */
.about{left:0;top:552px;width:1200px;height:466px;background:var(--mint)}
.about-photo{left:104px;top:604px;width:372px;height:372px;border-radius:50%;border:14px solid #c7d5b9;background:linear-gradient(135deg,#f2c9a0,#e8a7a0 50%,#86b6d6)}
.about-copy{left:508px;top:624px;width:665px}
.about-copy h2{font-size:26px;color:var(--leaf);letter-spacing:.5px}
.about-copy h3{font-size:16px;font-weight:700;color:#7e9a6a;margin:10px 0 12px}
.about-copy p{font-size:12.6px;line-height:1.55;margin-bottom:20px}

/* features */
.features{left:0;top:1018px;width:1200px;height:692px;background:var(--feature-green)}
.section-title{left:0;width:1200px;text-align:center;font-size:35px}
.features .section-title{top:1064px;color:var(--white)}
.feature-photo{top:1145px;width:336px;height:336px;border-radius:50%}
.feature-caption{top:1500px;width:340px;text-align:center;color:var(--white);font-family:"Fredoka",sans-serif;font-weight:600;font-size:21px;line-height:1.2}
.feature-btn{top:1573px;width:142px;height:28px;background:var(--leaf-dark);color:var(--white);font-size:11px;font-weight:600;text-align:center;line-height:28px}
.dots{display:flex;gap:6px}
.dots i{display:block;width:15px;height:15px;border-radius:50%;background:#dfe9d4}
.dots i.on{background:var(--white)}

/* testimonial */
.testimonial{left:0;top:1710px;width:1200px;height:486px;background:var(--sage)}
.testimonial .section-title{top:1755px;color:var(--leaf)}
.avatar{left:545px;top:1840px;width:108px;height:108px;border-radius:50%;border:4px solid var(--white);background:linear-gradient(135deg,#e9b48e,#c8876a)}
.quote{left:240px;top:1962px;width:720px;text-align:center;font-size:18px;line-height:1.5;color:#333}
.author{left:0;top:2062px;width:1200px;text-align:center;font-size:13px;font-weight:700}
.testimonial .dots i{background:var(--white)}
.testimonial .dots i.on{background:var(--leaf)}

/* contact */
.contact{left:0;top:2196px;width:1200px;height:822px;background:var(--mint)}
.contact .section-title{top:2240px;color:var(--leaf)}
.info-box{left:120px;width:363px;height:123px;background:var(--box-sage);border-radius:6px;text-align:center;padding-top:38px}
.info-box h4{font-family:"Fredoka",sans-serif;font-weight:600;color:var(--leaf);font-size:16px;margin-bottom:6px}
.info-box p{font-size:13.5px;line-height:1.45}
.info-icon{left:270px}
.field{background:var(--mint);border:1.5px solid #b7c9a4;border-radius:6px;height:44px;padding:0 18px;line-height:42px;font-size:13px;color:#8a9a80}
.send-btn{left:518px;top:2601px;width:147px;height:42px;background:var(--leaf);color:var(--white);border-radius:6px;text-align:center;line-height:42px;font-size:14px;font-weight:700}
.map{left:120px;top:2697px;width:957px;height:267px;border:2px solid #d3dccb;border-radius:6px;background:linear-gradient(135deg,#eef0e6,#e4e8dc 50%,#dfe9d6)}

/* footer */
.footer{left:0;top:3018px;width:1200px;height:661px;background:var(--footer-green)}
.footer-box{top:3065px;height:292px;border:2px solid #d5e4c6;border-radius:10px;padding:26px 22px;color:var(--white)}
.footer-box h5{font-family:"Montserrat",sans-serif;font-size:16px;font-weight:700;margin-bottom:14px}
.footer-box p{font-size:12px;line-height:1.65}
.footer-box ul{list-style:none;font-size:12px;line-height:1.4}
.footer-box li{position:relative;padding-left:18px;margin-bottom:12px}
.footer-box li::before{content:"";position:absolute;left:0;top:4px;width:9px;height:9px;border-radius:50%;background:#e3efd6}
.eclub-outline{display:inline-block;margin-top:30px;padding:0 22px;height:30px;line-height:30px;background:#9dbb80;color:var(--white);font-size:11px;border-radius:3px}
.footer-brand{left:0;top:3410px;width:1200px;text-align:center;color:var(--white);font-family:"Fredoka",sans-serif;font-weight:500;line-height:1}
.footer-brand .name{font-size:42px;letter-spacing:1px}
.footer-brand .tag{font-size:23px;margin-top:2px}
.social{top:3517px;width:34px;height:34px;border-radius:50%;border:2.5px solid var(--white)}
.copyright{left:0;top:3582px;width:1200px;text-align:center;color:var(--white);font-size:10px;font-weight:700;letter-spacing:.3px}
</style>
</head>
<body>

<section class="abs hero" role="img" aria-label="Photo of smiling children drawing at a classroom table"></section>
<div class="abs menu-toggle"><span></span><span></span><span></span></div>
<div class="abs brand"><div class="name">Tumble Nest</div><div class="tag">Playhouse &amp; Cafe</div></div>
<div class="abs eclub-btn">Join Our E-club</div>
<div class="abs hero-phone">Call: 02 9000 1100</div>
<h1 class="abs hero-title">So much fun for everyone</h1>

<section class="abs about"></section>
<div class="abs about-photo" role="img" aria-label="Photo of children painting with a parent at the play centre"></div>
<div class="abs about-copy">
  <h2 class="heading">ABOUT TUMBLE NEST PLAYHOUSE &amp; CAFE</h2>
  <h3>Welcome to Tumble Nest, Sydney's newest and best party &amp; play centre!</h3>
  <p>Tumble Nest is an indoor Kids Play Centre and Cafe that offers both kids and adults a chance to enjoy their time, together! We pride ourselves in offering the best indoor play centre for your kids to engage in fun and learning activities in a specially created environment that is not only warm and safe but also enhances and stimulates creativity and curiosity in a child. Tumble Nest offers variety of kids party venues like our themed party rooms which are hand painted.</p>
  <p>Tumble Nest has entertained over 1 million children. Our party rooms are unarguably the best in Sydney and were designed by an internationally renowned artist who was commissioned from England and has won numerous awards. She was specially flown to Australia to design and hand paint our party rooms. We aim to ensure that every party you host at Tumble Nest is not only fun but memorable and our comprehensive planning and facilities offer fun, excitement and entertainment for kids of all ages.</p>
</div>

<section class="abs features" role="img" aria-label="Faded photo of children playing, tinted green"></section>
<h2 class="abs heading section-title" style="top:1064px;color:var(--white)">Our Features</h2>
<div class="abs feature-photo" style="left:77px;background:linear-gradient(135deg,#5a3b2c,#b3784e 55%,#e2c39b)" role="img" aria-label="Photo of a family birthday party with cake"></div>
<div class="abs feature-photo" style="left:433px;background:linear-gradient(135deg,#7a3f6e,#d9577e 50%,#86c04f)" role="img" aria-label="Photo of a themed party room with balloons and an entertainer"></div>
<div class="abs feature-photo" style="left:784px;background:linear-gradient(135deg,#c93c3c,#f0d23a 50%,#b8b9b5)" role="img" aria-label="Photo of costumed characters at a school holiday program"></div>
<div class="abs feature-caption" style="left:75px">Perfect venue for<br>birthdays and private parties</div>
<div class="abs feature-caption" style="left:431px">4 kids loving<br>party rooms themes</div>
<div class="abs feature-caption" style="left:782px">We host school<br>holiday programs</div>
<div class="abs feature-btn" style="left:175px">VIEW PARTIES</div>
<div class="abs feature-btn" style="left:531px">VIEW PARTY ROOMS</div>
<div class="abs feature-btn" style="left:882px">VIEW PROGRAMS</div>
<div class="abs dots" style="left:570px;top:1661px"><i></i><i class="on"></i><i class="on"></i></div>

<section class="abs testimonial" role="img" aria-label="Soft chalkboard doodles background in green"></section>
<h2 class="abs heading section-title" style="top:1755px;color:var(--leaf)">What People Say About Us</h2>
<div class="abs avatar" role="img" aria-label="Customer portrait"></div>
<p class="abs quote">Had my son's birthday party there. Kids had such a great time I recommend this place to everyone.Staff are amazing. Food and coffee are delicious! Thank you</p>
<div class="abs author">Dana Hollis</div>
<div class="abs dots" style="left:570px;top:2128px"><i class="on"></i><i></i><i></i></div>

<section class="abs contact"></section>
<h2 class="abs heading section-title" style="top:2240px;color:var(--leaf)">Contact Us</h2>
<svg class="abs info-icon" style="left:276px;top:2282px" width="48" height="72" viewBox="0 0 48 72" aria-hidden="true">
  <path d="M24 3C12.4 3 4 11.6 4 23c0 15 20 40 20 40s20-25 20-40C44 11.6 35.6 3 24 3z" fill="none" stroke="#5d8c2e" stroke-width="5"/>
  <circle cx="24" cy="23" r="7" fill="none" stroke="#5d8c2e" stroke-width="5"/>
</svg>
<div class="abs info-box" style="top:2329px">
  <h4>Postal Address</h4>
  <p>14 Fernleigh Road Brookvale 2100<br>NSW Australia</p>
</div>
<svg class="abs" style="left:266px;top:2472px" width="68" height="64" viewBox="0 0 68 64" aria-hidden="true">
  <circle cx="34" cy="32" r="27" fill="none" stroke="#5d8c2e" stroke-width="5"/>
  <path d="M24 18c-4 3-4 9 1 17s12 13 17 12l4-5-7-6-4 3c-3-1-7-6-8-9l3-4-6-8z" fill="#5d8c2e"/>
</svg>
<div class="abs info-box" style="top:2523px">
  <h4>Phone &amp; E-mail</h4>
  <p>Ph: 02 9000 1100 | Fax: 02 9000 1199<br>Email: hello@tumblenest.com.au</p>
</div>
<div class="abs field" style="left:518px;top:2327px;width:268px">Your Name</div>
<div class="abs field" style="left:798px;top:2327px;width:270px">Phone</div>
<div class="abs field" style="left:518px;top:2388px;width:268px">Your Email</div>
<div class="abs field" style="left:798px;top:2388px;width:270px">Postcode</div>
<div class="abs field" style="left:518px;top:2447px;width:550px;height:137px;line-height:1;padding-top:14px">Your Message</div>
<div class="abs send-btn">Send Message</div>
<div class="abs map" role="img" aria-label="Street map of the Brookvale area with a location marker"></div>

<section class="abs footer" role="img" aria-label="Faded photo of children in the play area, tinted green"></section>
<div class="abs footer-box" style="left:120px;width:307px">
  <h5>ABOUT US</h5>
  <p>We welcome all the kids to come and play at our Brookvale indoor play centre. Our kids play centre features slides and lots of other fun activities. We also have a safe toddler area, while you enjoy a cup of coffee and cake, or some lunch from our extensive cafe menu where we only use the freshest "A" grade quality ingredients.</p>
  <span class="eclub-outline">JOIN OUR E-CLUB</span>
</div>
<div class="abs footer-box" style="left:444px;width:309px">
  <h5>OUR FEATURES</h5>
  <ul>
    <li>Ball pit</li>
    <li>Safe baby play area for 12 to 24 months</li>
    <li>4 x lane 6m slide</li>
    <li>Rock climbing</li>
    <li>Toddler &amp; younger kids play area for 2 to 5 years</li>
  </ul>
</div>
<div class="abs footer-box" style="left:773px;width:307px">
  <h5>BROOKVALE LATEST POSTS</h5>
  <p>No Recent Post available</p>
</div>
<div class="abs footer-brand"><div class="name">Tumble Nest</div><div class="tag">Playhouse &amp; Cafe</div></div>
<div class="abs social" style="left:561px" aria-label="Social link"></div>
<div class="abs social" style="left:603px" aria-label="Social link"></div>
<div class="abs copyright">SITE CONTENTS © 2016 WWW.TUMBLENEST.COM.AU</div>

</body>
</html>
```